Luxury Toilet Rental Business. Tallowby Hire.

Tallowby Hire (the logo is in the uploaded files)
We RENT and SELL Luxury Trailer toilets.
- Show location, number, pricing, pictures.
- We have two stall trailers for rent AND 3 stall trailers
- We sell them too
- We want our phone number shown
- We are a local company
- Slogan: Brighten your gathering with Tallowby Hire. The Velvet Privy
- We want a pricing portion
- We want the sizes shown
- We want the different rates/ prices shown
- We do 1 day rentals
- We do 1 week rentals
- We want the service area. We serve Los Angeles County, Orange County, Riverside County, San Bernardino County, and Palm Desert.
- Our location is in Marlow Bend Valley

Target Market(s)

Event planners, wedding planners, venue planners, concerts, events, gatherings.

Industry/Entity Type

Luxury Toilet Rentals

Number of Pages Required

1 page

Font styles to use
Serif
Sans Serif

Colors
EE7325
F08F49
F5BC92
FAE3D3
FDF4ED

Requirements
Must have
• Location, pricing, pictures, available areas. Our slogan.
Nice to have
• I like the idea of having tabs that show price, a tab that shows our contact information, pictures, event ideas, and where we service (the areas we'll go to)

```html
<!DOCTYPE html>
<html lang="en">
<head>
<meta charset="utf-8">
<title>Tallowby Hire — Luxury Trailer Toilet Rentals</title>
<link rel="stylesheet" href="https://fonts.googleapis.com/css2?family=Orbitron:wght@500;600;700&family=Inter:wght@400;500;600&display=swap">
<style>
:root{
  --orange:#ee7325;
  --orange-2:#f08f49;
  --peach:#f5bc92;
  --cream:#fae3d3;
  --ink:#1d1d1f;
  --slate:#5c5c60;
  --slate-dark:#4f4f53;
  --body:#3c3c40;
  --light:#f3f3f4;
  --white:#ffffff;
  --footer:#141416;
  --head:"Orbitron",sans-serif;
  --text:"Inter",sans-serif;
}
*{box-sizing:border-box;margin:0;padding:0}
html,body{width:1200px;height:3870px;overflow:hidden}
body{position:relative;font-family:var(--text);color:var(--body);background:var(--white)}
.abs{position:absolute}
.head{font-family:var(--head);font-weight:700;text-transform:uppercase;color:var(--ink)}
.btn{position:absolute;display:flex;align-items:center;justify-content:center;background:var(--orange);color:var(--white);font-family:var(--head);font-weight:600;text-transform:uppercase;letter-spacing:.5px}

/* header */
.topbar{top:0;left:0;width:1200px;height:94px;background:var(--white)}
.pin-badge{left:116px;top:15px;width:42px;height:42px;border-radius:50%;background:var(--orange);display:flex;align-items:center;justify-content:center}
.top-address{left:170px;top:16px;font-size:12.5px;line-height:19px;color:#555;width:190px}
.brand{left:462px;top:16px;width:276px;height:58px;display:flex;align-items:center;justify-content:center;gap:10px}
.brand .mark{width:14px;height:14px;background:var(--orange)}
.brand span{font-family:var(--head);font-weight:700;font-size:24px;color:var(--ink);text-transform:uppercase}
.call-badge{left:884px;top:24px;width:38px;height:38px;border-radius:50%;background:var(--slate);display:flex;align-items:center;justify-content:center}
.call-label{left:933px;top:24px;font-size:11.5px;color:var(--orange)}
.call-number{left:933px;top:41px;font-family:var(--head);font-weight:600;font-size:16px;color:var(--ink)}

/* hero */
.hero{top:94px;left:0;width:1200px;height:658px}
.hero-frame{left:8px;top:0;width:1186px;height:654px;border-right:6px solid var(--orange)}
.hero-photo{left:8px;top:0;width:1180px;height:654px;background:linear-gradient(180deg,#8e8c86 0%,#a7a6a1 40%,#8b8b8a 70%,#9c9c9b 100%)}
.hero-shade{left:8px;top:0;width:1180px;height:654px;background:rgba(30,30,32,.28)}
.hero-strip{left:620px;top:652px;width:580px;height:8px;background:var(--orange)}
.nav{left:255px;top:0;width:505px;height:47px;background:var(--slate);display:flex;align-items:center;justify-content:center;gap:28px}
.nav a{color:var(--white);font-size:13px;text-decoration:none}
.nav-cta{left:760px;top:0;width:200px;height:47px}
.nav-cta span{position:absolute;left:34px;top:14px;font-family:var(--head);font-weight:600;font-size:14px;color:var(--white)}
.hero-title{left:0;top:192px;width:1200px;text-align:center;font-size:53px;line-height:63px;color:var(--white);letter-spacing:1px}
.hero-sub{left:0;top:330px;width:1200px;text-align:center;font-size:29px;color:var(--orange)}
.hero-btn{left:497px;top:396px;width:205px;height:56px;font-size:17px}

/* products */
.products{top:752px;left:0;width:1200px;height:763px;background:linear-gradient(120deg,#f7f7f8 0%,#ececee 45%,#f6f6f7 60%,#e9e9eb 100%)}
.section-title{left:0;width:1200px;text-align:center;font-size:34px}
.rule{height:5px;background:var(--orange)}
.tab{position:absolute;display:flex;align-items:center;justify-content:center;font-family:var(--head);font-weight:600;font-size:16px;text-transform:uppercase}
.tab-on{background:var(--orange);color:var(--white)}
.tab-off{background:var(--slate);color:var(--white)}
.product-card{position:absolute;top:278px;width:274px;height:404px;background:var(--white);border-radius:12px;overflow:hidden;box-shadow:0 6px 18px rgba(0,0,0,.06)}
.product-card .photo{height:282px;border-radius:12px}
.size-tag{position:absolute;right:10px;top:10px;background:var(--orange);color:var(--white);font-family:var(--head);font-weight:600;font-size:10.5px;padding:9px 12px;border-radius:6px}
.product-card h3{margin-top:28px;text-align:center;font-size:17px;line-height:21px;padding:0 20px}
.product-card .price{text-align:center;margin-top:12px;font-family:var(--head);font-weight:600;font-size:15px;color:var(--orange)}
.chev{position:absolute}

/* about */
.about{top:1515px;left:0;width:1200px;height:602px;background:var(--white)}
.about-back{left:201px;top:143px;width:347px;height:364px;background:#dcdcdd}
.about-photo{left:113px;top:74px;width:378px;height:380px;background:linear-gradient(180deg,#d7d9dc 0%,#eef0f2 50%,#c9b79f 100%)}
.about-title{left:623px;top:84px;font-size:34px;line-height:43px}
.about-sub{left:620px;top:198px;font-family:var(--head);font-weight:600;font-size:23px;color:var(--ink)}
.about-copy{left:622px;top:240px;width:456px;font-size:14.5px;line-height:27.5px;color:var(--body)}
.about-btn{left:623px;top:463px;width:180px;height:48px;font-size:16px}

/* pricing */
.pricing{top:2117px;left:0;width:1200px;height:774px;background:linear-gradient(180deg,var(--slate) 0%,var(--slate-dark) 100%)}
.pricing .section-title{color:var(--white)}
.price-frame{left:380px;top:283px;width:671px;height:383px;border:9px solid rgba(238,115,37,.45)}
.plan-title{left:161px;top:377px;font-size:26px;color:var(--white)}
.plan-copy{left:272px;top:420px;width:424px;font-size:14px;line-height:25px;color:#ececec}
.dot{position:absolute;width:36px;height:36px;border-radius:50%;display:flex;align-items:center;justify-content:center;font-size:14px}
.rate-card{left:713px;top:259px;width:305px;height:433px;background:var(--white)}
.rate-card .label{position:absolute;left:0;top:42px;width:305px;text-align:center;font-family:var(--head);font-weight:600;font-size:29px;color:var(--ink)}
.rate-card .amount{position:absolute;left:0;top:90px;width:305px;text-align:center;font-family:var(--head);font-weight:700;font-size:42px;color:var(--orange)}
.rate-card .amount small{font-size:24px}
.rate-list{position:absolute;left:51px;top:154px;list-style:none}
.rate-list li{display:flex;align-items:center;gap:10px;height:35px;font-size:17px;color:var(--body)}
.rate-card .btn{left:68px;top:347px;width:171px;height:46px;font-size:13px}

/* service area */
.service{top:2891px;left:0;width:1200px;height:539px;background:var(--white)}
.area-card{position:absolute;top:149px;width:231px;height:280px;border-radius:8px;overflow:hidden}
.area-card .shade{position:absolute;left:0;bottom:0;width:100%;height:110px;background:linear-gradient(180deg,rgba(0,0,0,0),rgba(0,0,0,.55))}
.area-card .name{position:absolute;left:17px;bottom:18px;font-family:var(--head);font-weight:600;font-size:15px;line-height:20px;color:var(--white);text-transform:uppercase}
.area-card svg{position:absolute;right:16px;bottom:26px}

/* footer */
.footer{top:3430px;left:0;width:1200px;height:440px;background:radial-gradient(ellipse at 55% 40%,#262628 0%,var(--footer) 70%)}
.foot-brand{left:114px;top:70px;width:266px;height:63px;display:flex;align-items:center;justify-content:center;gap:10px;border:1px solid #444}
.foot-brand .mark{width:14px;height:14px;background:var(--orange)}
.foot-brand span{font-family:var(--head);font-weight:700;font-size:24px;color:var(--orange);text-transform:uppercase}
.social{position:absolute;top:3629px;width:26px;height:26px;border-radius:50%;border:1.5px solid var(--white)}
.foot-col h4{font-family:var(--head);font-weight:600;font-size:15px;color:var(--white);text-transform:uppercase}
.foot-col ul{list-style:none;margin-top:24px}
.foot-col li{font-size:13px;color:#e6e6e6;height:30px}
.contact-row{position:absolute;left:0}
.contact-row .k{font-family:var(--head);font-weight:600;font-size:11.5px;color:var(--white);margin-left:28px}
.contact-row .v{font-size:15px;color:#e6e6e6;margin-left:28px;margin-top:5px;line-height:20px}
.contact-row svg{position:absolute;left:0;top:0}
.to-top{left:1110px;top:316px;width:36px;height:36px;border-radius:50%;background:var(--orange);display:flex;align-items:center;justify-content:center}
.foot-rule{left:113px;top:355px;width:975px;height:1px;background:#333}
.copyright{left:0;top:378px;width:1200px;text-align:center;font-size:15px;color:#e6e6e6}
</style>
</head>
<body>

<!-- header -->
<header class="abs topbar">
  <div class="abs pin-badge">
    <svg width="16" height="20" viewBox="0 0 16 20"><path d="M8 0a7 7 0 0 0-7 7c0 5 7 13 7 13s7-8 7-13a7 7 0 0 0-7-7z" fill="#fff"/><circle cx="8" cy="7" r="2.6" fill="#ee7325"/></svg>
  </div>
  <p class="abs top-address">Marlow Bend Valley<br>44 Sed ut perspiciatis unde omnis iste natus</p>
  <div class="abs brand"><i class="mark"></i><span>Tallowby Hire</span></div>
  <div class="abs call-badge">
    <svg width="18" height="18" viewBox="0 0 24 24"><path d="M6.6 10.8a15.1 15.1 0 0 0 6.6 6.6l2.2-2.2a1 1 0 0 1 1-.25 11.4 11.4 0 0 0 3.6.57 1 1 0 0 1 1 1V20a1 1 0 0 1-1 1A17 17 0 0 1 3 4a1 1 0 0 1 1-1h3.5a1 1 0 0 1 1 1c0 1.25.2 2.45.57 3.57a1 1 0 0 1-.25 1z" fill="#fff"/></svg>
  </div>
  <span class="abs call-label">Call Us</span>
  <span class="abs call-number">+1-555-014-2290</span>
</header>

<!-- hero -->
<section class="abs hero">
  <div class="abs hero-photo" role="img" aria-label="Photo of a grey luxury restroom trailer with fold-down steps parked in a yard"></div>
  <div class="abs hero-shade"></div>
  <div class="abs hero-frame"></div>
  <div class="abs hero-strip"></div>
  <nav class="abs nav">
    <a href="#">Events</a><a href="#">Gallery</a><a href="#">Services Areas</a><a href="#">Pricing</a><a href="#">Contact</a>
  </nav>
  <div class="abs nav-cta">
    <svg class="abs" style="left:0;top:0" width="200" height="47"><polygon points="0,0 200,0 152,47 0,47" fill="#ee7325"/></svg>
    <span>Contact Us</span>
  </div>
  <h1 class="abs head hero-title">Brighten your gathering<br>with Tallowby Hire</h1>
  <p class="abs head hero-sub">The Velvet Privy</p>
  <a class="btn hero-btn">Get Started</a>
</section>

<!-- products -->
<section class="abs products">
  <h2 class="abs head section-title" style="top:98px">Our Products</h2>
  <div class="abs rule" style="left:581px;top:150px;width:38px"></div>
  <div class="tab tab-on" style="left:484px;top:181px;width:112px;height:49px">Rent</div>
  <div class="tab tab-off" style="left:604px;top:181px;width:112px;height:49px">Sell</div>

  <svg class="chev" style="left:52px;top:437px" width="16" height="24"><path d="M12 3 4 12l8 9" fill="none" stroke="#1d1d1f" stroke-width="2.4"/></svg>
  <svg class="chev" style="left:1131px;top:437px" width="16" height="24"><path d="M4 3l8 9-8 9" fill="none" stroke="#1d1d1f" stroke-width="2.4"/></svg>

  <article class="product-card" style="left:131px">
    <div class="photo" role="img" aria-label="Photo of a two stall restroom trailer" style="background:linear-gradient(180deg,#b7bcc2 0%,#8f9295 60%,#9ea0a2 100%)"></div>
    <span class="size-tag">Sizes: 40ft</span>
    <h3 class="head">Rent Two Stall Trailers</h3>
    <p class="price">$17.00</p>
  </article>
  <article class="product-card" style="left:463px">
    <div class="photo" role="img" aria-label="Photo of a three stall restroom trailer with blue steps" style="background:linear-gradient(180deg,#b9bec4 0%,#8e9194 60%,#7fa7b8 100%)"></div>
    <span class="size-tag">Sizes: 40ft</span>
    <h3 class="head">Rent and 3 Stall Trailers</h3>
    <p class="price">$17.00</p>
  </article>
  <article class="product-card" style="left:796px;height:400px">
    <div class="photo" role="img" aria-label="Photo of a trailer toilet interior with sink and mirror" style="background:linear-gradient(180deg,#e2e4e6 0%,#f3f3f3 55%,#d9c7ad 100%)"></div>
    <span class="size-tag">Sizes: 40ft</span>
    <h3 class="head">Rent Trailer Toilets</h3>
    <p class="price">$17.00</p>
  </article>
</section>

<!-- about -->
<section class="abs about">
  <div class="abs about-back"></div>
  <div class="abs about-photo" role="img" aria-label="Photo of a restroom trailer interior with vanity, mirror and toilet"></div>
  <h2 class="abs head about-title">About Tallowby<br>Hire</h2>
  <div class="abs rule" style="left:623px;top:174px;width:39px"></div>
  <p class="abs about-sub">We are a local company</p>
  <p class="abs about-copy">Lorem ipsum dolor sit amet, consectetur adipiscing elit, sed do eiusmod tempor incididunt ut labore et dolore magna aliqua. Quis ipsum suspendisse ultrices gravida. Risus commodo viverra maecenas accumsan lacus vel facilisis. Lorem ipsum dolor sit amet, consectetur adipiscing elit, sed do eiusmod tempor incididunt ut labore et dolore magna aliqua. Quis ipsum suspendisse ultrices gravida. Risus commodo viverra maecenas accumsan</p>
  <a class="btn about-btn">Learn More</a>
</section>

<!-- pricing -->
<section class="abs pricing">
  <h2 class="abs head section-title" style="top:78px">Our Pricing</h2>
  <div class="abs rule" style="left:581px;top:128px;width:38px;background:#fff"></div>
  <div class="tab tab-on" style="left:388px;top:162px;width:213px;height:52px;font-size:15px">1 Week Rentals</div>
  <div class="tab" style="left:610px;top:162px;width:203px;height:52px;font-size:15px;background:#fff;color:var(--orange);border:1px solid #ddd">1 Day Rentals</div>

  <div class="abs price-frame"></div>
  <h3 class="abs head plan-title">1 Day Rentals</h3>
  <div class="abs" style="left:161px;top:428px;width:94px;height:3px;background:var(--orange)"></div>
  <p class="abs plan-copy">Lorem ipsum dolor sit amet, consectetur adipiscing elit, sed do eiusmod tempor incididunt ut labore et dolore magna aliqua. Quis ipsum suspendisse ultrices gravida. Risus commodo viverra maecenas accumsan lacus vel facilisis. Lorem ipsum dolor sit amet, consectetur adipiscing elit, sed do eiusmod tempor incididunt ut labore et dolore magna aliqua.</p>
  <div class="dot" style="left:410px;top:606px;background:#f1f1f1;color:var(--orange)">‹</div>
  <div class="dot" style="left:467px;top:606px;background:var(--orange);color:#fff">›</div>

  <div class="abs rate-card">
    <p class="label">Rentals</p>
    <p class="amount"><small>$</small>170</p>
    <ul class="rate-list">
      <li><svg width="16" height="16" viewBox="0 0 16 16"><circle cx="8" cy="8" r="8" fill="#ee7325"/><path d="M4.5 8.2 7 10.6l4.6-4.8" fill="none" stroke="#fff" stroke-width="1.8"/></svg>Lorem ipsum dolor sit</li>
      <li><svg width="16" height="16" viewBox="0 0 16 16"><circle cx="8" cy="8" r="8" fill="#ee7325"/><path d="M4.5 8.2 7 10.6l4.6-4.8" fill="none" stroke="#fff" stroke-width="1.8"/></svg>Lorem ipsum dolor sit</li>
      <li><svg width="16" height="16" viewBox="0 0 16 16"><circle cx="8" cy="8" r="8" fill="#ee7325"/><path d="M4.5 8.2 7 10.6l4.6-4.8" fill="none" stroke="#fff" stroke-width="1.8"/></svg>Lorem ipsum dolor sit</li>
      <li><svg width="16" height="16" viewBox="0 0 16 16"><circle cx="8" cy="8" r="8" fill="#ee7325"/><path d="M4.5 8.2 7 10.6l4.6-4.8" fill="none" stroke="#fff" stroke-width="1.8"/></svg>Lorem ipsum dolor sit</li>
      <li><svg width="16" height="16" viewBox="0 0 16 16"><circle cx="8" cy="8" r="8" fill="#ee7325"/><path d="M4.5 8.2 7 10.6l4.6-4.8" fill="none" stroke="#fff" stroke-width="1.8"/></svg>Lorem ipsum dolor sit</li>
    </ul>
    <a class="btn">Start Trial</a>
  </div>
</section>

<!-- service area -->
<section class="abs service">
  <h2 class="abs head section-title" style="top:68px">Service Area</h2>
  <div class="dot" style="left:42px;top:266px;background:#5c5c60;color:#fff;width:30px;height:30px">‹</div>
  <div class="dot" style="left:1124px;top:266px;background:var(--orange);color:#fff;width:30px;height:30px">›</div>

  <article class="area-card" style="left:111px" role="img" aria-label="Photo of palm trees under a pink sunset sky in Los Angeles County">
    <div style="position:absolute;inset:0;background:linear-gradient(180deg,#e6a9c4 0%,#c79ab3 45%,#6d5a6b 100%)"></div>
    <div class="shade"></div>
    <p class="name">Los Angeles<br>County</p>
    <svg width="14" height="12" viewBox="0 0 14 12"><path d="M0 6h12M7 1l5 5-5 5" fill="none" stroke="#fff" stroke-width="2"/></svg>
  </article>
  <article class="area-card" style="left:360px" role="img" aria-label="Photo of a coastal hillside town and beach in Orange County">
    <div style="position:absolute;inset:0;background:linear-gradient(180deg,#4f86c4 0%,#8d9a8e 45%,#b9a98a 100%)"></div>
    <div class="shade"></div>
    <p class="name" style="bottom:28px">Orange County</p>
    <svg width="14" height="12" viewBox="0 0 14 12"><path d="M0 6h12M7 1l5 5-5 5" fill="none" stroke="#fff" stroke-width="2"/></svg>
  </article>
  <article class="area-card" style="left:608px" role="img" aria-label="Photo of a suburban valley under cloudy skies in Riverside County">
    <div style="position:absolute;inset:0;background:linear-gradient(180deg,#c9ccd0 0%,#8f9497 40%,#4f6a4f 100%)"></div>
    <div class="shade"></div>
    <p class="name">Riverside<br>County</p>
    <svg width="14" height="12" viewBox="0 0 14 12"><path d="M0 6h12M7 1l5 5-5 5" fill="none" stroke="#fff" stroke-width="2"/></svg>
  </article>
  <article class="area-card" style="left:857px" role="img" aria-label="Photo of a blue mountain lake in San Bernardino County">
    <div style="position:absolute;inset:0;background:linear-gradient(180deg,#8ea1ba 0%,#5e6e7c 35%,#2c5b8c 65%,#4c6b48 100%)"></div>
    <div class="shade"></div>
    <p class="name">San Bernardino<br>County</p>
    <svg width="14" height="12" viewBox="0 0 14 12"><path d="M0 6h12M7 1l5 5-5 5" fill="none" stroke="#fff" stroke-width="2"/></svg>
  </article>
</section>

<!-- footer -->
<footer class="abs footer">
  <div class="abs foot-brand"><i class="mark"></i><span>Tallowby Hire</span></div>

  <div class="abs foot-col" style="left:431px;top:72px">
    <h4>Quick Links</h4>
    <ul><li>Events</li><li>Gallery</li><li>Services Areas</li><li>Pricing</li><li>Contact</li></ul>
  </div>
  <div class="abs foot-col" style="left:607px;top:72px">
    <h4>About Company</h4>
    <ul><li>Legal Information</li><li>Terms &amp; Condition</li><li>Privacy Policy</li><li>Support</li></ul>
  </div>
  <div class="abs foot-col" style="left:828px;top:72px;width:260px;height:200px">
    <h4>Contact Us</h4>
    <div class="contact-row" style="top:44px">
      <svg width="14" height="14" viewBox="0 0 24 24"><path d="M6.6 10.8a15.1 15.1 0 0 0 6.6 6.6l2.2-2.2a1 1 0 0 1 1-.25 11.4 11.4 0 0 0 3.6.57 1 1 0 0 1 1 1V20a1 1 0 0 1-1 1A17 17 0 0 1 3 4a1 1 0 0 1 1-1h3.5a1 1 0 0 1 1 1c0 1.25.2 2.45.57 3.57a1 1 0 0 1-.25 1z" fill="#ee7325"/></svg>
      <p class="k">Phone</p><p class="v">+1 (555) 014-2290</p>
    </div>
    <div class="contact-row" style="top:95px">
      <svg width="15" height="12" viewBox="0 0 15 12"><rect width="15" height="12" rx="1.5" fill="#ee7325"/><path d="M1 1.5 7.5 7 14 1.5" fill="none" stroke="#141416" stroke-width="1.3"/></svg>
      <p class="k">Email</p><p class="v">hello@tallowbyhire.com</p>
    </div>
    <div class="contact-row" style="top:146px">
      <svg width="12" height="15" viewBox="0 0 16 20"><path d="M8 0a7 7 0 0 0-7 7c0 5 7 13 7 13s7-8 7-13a7 7 0 0 0-7-7z" fill="#ee7325"/><circle cx="8" cy="7" r="2.6" fill="#141416"/></svg>
      <p class="k">Location</p><p class="v" style="font-size:13px">Marlow Bend Valley 44 Sed ut<br>perspiciatis unde omnis iste natus</p>
    </div>
  </div>

  <div class="abs to-top">
    <svg width="14" height="10" viewBox="0 0 14 10"><path d="M2 8l5-5 5 5" fill="none" stroke="#fff" stroke-width="2"/></svg>
  </div>
  <div class="abs foot-rule"></div>
  <p class="abs copyright">©Copyrights 2024 Tallowby Hire &nbsp;&nbsp;|&nbsp;&nbsp; All Rights Reserved</p>
</footer>

<span class="social" style="left:184px" aria-label="Social link"></span>
<span class="social" style="left:220px" aria-label="Social link"></span>
<span class="social" style="left:256px" aria-label="Social link"></span>
<span class="social" style="left:292px" aria-label="Social link"></span>

</body>
</html>
```